Simple and Clean business card design

We would like the design to be simple clean and to incorporate our colors.

We are open to your design and talent, we have the dots in our logo as we think of it as data points and we connect data points for people.

We are open to see the great creative and clean design you bring to the table

Contact Information for Business Card

please include: name, position, email, phone and website

Font styles to use
Sans Serif

Requirements
Must have
• my colors incorporated, simplicity
Nice to have
• lots of white space, simplicity
Should not have
• complexicity/ complex art

```html
<!DOCTYPE html>
<html lang="en">
<head>
<meta charset="utf-8">
<title>Nodera — Business Card</title>
<link rel="stylesheet" href="https://fonts.googleapis.com/css2?family=Open+Sans:wght@400;600&family=Oswald:wght@700&family=Saira:wght@600&display=swap">
<style>
  :root {
    --page: #fdfdfd;
    --card-white: #ffffff;
    --brand-blue: #4285f4;
    --ink: #1a1a1a;
    --wordmark-ink: #0a0a0a;
    --faint-mark: #e8ecf5;
    --card-edge: #c9c9c9;
    --white: #ffffff;
  }
  * { margin: 0; padding: 0; box-sizing: border-box; }
  html, body {
    width: 1200px; height: 1200px; overflow: hidden;
    background: var(--page);
    font-family: "Open Sans", sans-serif;
  }
  .canvas { position: relative; width: 1200px; height: 1200px; }

  .card {
    position: absolute; top: 211px; width: 457px; height: 785px; overflow: hidden;
  }
  .card--front { left: 136px; background: var(--card-white); border: 1px solid var(--card-edge); }
  .card--back { left: 627px; background: var(--brand-blue); }

  .brand-lockup {
    position: absolute; display: flex; align-items: flex-start; gap: 8px;
  }
  .wordmark {
    font-family: "Open Sans", sans-serif; font-weight: 600;
    letter-spacing: -1px; line-height: 1; white-space: nowrap;
  }
  .brand-dot { flex: none; border-radius: 50%; }

  .front-lockup { left: 78px; top: 137px; }
  .front-lockup .wordmark { font-size: 85px; color: var(--wordmark-ink); }
  .front-lockup .brand-dot { width: 18px; height: 18px; margin-top: 4px; background: var(--brand-blue); }

  .faint-wordmark {
    position: absolute; left: 7px; top: 617px;
    font-size: 127px; color: var(--faint-mark); letter-spacing: -2px;
  }

  .holder-name {
    position: absolute; left: 27px; top: 348px;
    font-family: "Oswald", sans-serif; font-weight: 700; font-size: 44px;
    color: var(--brand-blue); letter-spacing: 1px; line-height: 1;
  }
  .holder-role {
    position: absolute; left: 27px; top: 401px;
    font-family: "Saira", sans-serif; font-weight: 600; font-size: 15.5px;
    letter-spacing: 1.6px; color: var(--ink); line-height: 1;
  }
  .role-rule {
    position: absolute; left: 163px; top: 407px; width: 263px; height: 2px;
    background: var(--brand-blue);
  }

  .contact-list { position: absolute; left: 29px; top: 463px; list-style: none; }
  .contact-item { display: flex; align-items: center; height: 37px; margin-bottom: 10px; }
  .contact-icon {
    width: 37px; height: 37px; border: 2px solid var(--brand-blue); border-radius: 6px;
    display: flex; align-items: center; justify-content: center; margin-right: 15px;
  }
  .contact-icon svg { width: 22px; height: 22px; }
  .contact-text { font-size: 21px; color: var(--ink); }

  .address {
    position: absolute; left: 27px; top: 624px; font-size: 18px; line-height: 25px;
    color: var(--ink); text-transform: uppercase;
  }

  .back-rule { position: absolute; top: 387px; width: 66px; height: 2px; background: var(--white); }
  .back-rule--left { left: 6px; }
  .back-rule--right { left: 375px; }
  .back-lockup { left: 0; right: 0; top: 365px; justify-content: center; }
  .back-lockup .wordmark { font-size: 61px; color: var(--white); }
  .back-lockup .brand-dot { width: 12px; height: 12px; margin-top: 6px; background: var(--white); }
</style>
</head>
<body>
<main class="canvas">
  <section class="card card--front">
    <div class="wordmark faint-wordmark" aria-hidden="true">Nodera</div>
    <div class="brand-lockup front-lockup">
      <span class="wordmark">Nodera</span>
      <span class="brand-dot"></span>
    </div>

    <h1 class="holder-name">TOBIN KESSLY</h1>
    <p class="holder-role">CEO/FOUNDER</p>
    <span class="role-rule"></span>

    <ul class="contact-list">
      <li class="contact-item">
        <span class="contact-icon">
          <svg viewBox="0 0 24 24"><path fill="#4285f4" d="M6.6 3.2c.6-.4 1.3-.2 1.6.4l1.6 3c.3.6.1 1.2-.4 1.6l-1.1.7c.8 2.4 2.7 4.8 5 6.3l1-.9c.5-.4 1.2-.4 1.7 0l2.6 2.1c.5.4.6 1.2.1 1.7l-1.3 1.5c-.6.7-1.6.9-2.5.5-4.6-2.2-8.2-6.4-9.6-11.3-.3-.9 0-1.9.8-2.5z"/></svg>
        </span>
        <span class="contact-text">555-214-0387</span>
      </li>
      <li class="contact-item">
        <span class="contact-icon">
          <svg viewBox="0 0 24 24" fill="none" stroke="#4285f4" stroke-width="1.6"><rect x="2" y="5" width="20" height="14" fill="#4285f4" stroke="none"/><path d="M2 5l10 8 10-8M2 19l8-7M22 19l-8-7" stroke="#fff"/></svg>
        </span>
        <span class="contact-text">www.nodera.co</span>
      </li>
      <li class="contact-item">
        <span class="contact-icon">
          <svg viewBox="0 0 24 24" fill="none" stroke="#4285f4" stroke-width="1.2"><circle cx="12" cy="12" r="9"/><ellipse cx="12" cy="12" rx="4" ry="9"/><path d="M3 12h18M4.5 7.5h15M4.5 16.5h15M12 3v18"/></svg>
        </span>
        <span class="contact-text">tobin.kessly@nodera.co</span>
      </li>
    </ul>

    <p class="address">Address line goes here<br>Street name, country name</p>
  </section>

  <section class="card card--back">
    <span class="back-rule back-rule--left"></span>
    <div class="brand-lockup back-lockup">
      <span class="brand-dot"></span>
      <span class="wordmark">Nodera</span>
    </div>
    <span class="back-rule back-rule--right"></span>
  </section>
</main>
</body>
</html>
```